Storm Restoration Contractor needs a professional letterhead design

Looking for a professional letterhead design. Not looking for your cheapo MS Word standard ones that are readily available. Dont want it to be cookie cutter look like ones readily available online. We just recently changed our logo and want to freshen up all our documents. Our company handles restoring a property back to a pre-loss condition after a storm damages it. For example, wind, hail, flood, fire losses.

Target Market(s)

Property Owners, Homeowners, Property Owners, Commercial Property Owners, Property Management Companies

Industry/Entity Type

Construction Company

Requirements
Must have
• Professional, Use 1 of 2 logo options
• Storm Restoration, Roofing, Siding, Windows

```html
<!DOCTYPE html>
<html lang="en">
<head>
<meta charset="utf-8">
<title>Northgate Exteriors Letterhead</title>
<link rel="stylesheet" href="https://fonts.googleapis.com/css2?family=Open+Sans:wght@400;600;700&display=swap">
<style>
  :root {
    --brand-blue: #1f7ac4;
    --brand-grey: #55575b;
    --text-grey: #6a6c70;
    --heading-grey: #3c3e42;
    --backdrop: #ececec;
    --paper: #ffffff;
    --signature-tone: #d9dadd;
  }
  * { box-sizing: border-box; margin: 0; padding: 0; }
  html, body { width: 1200px; height: 936px; overflow: hidden; }
  body {
    background: var(--backdrop);
    font-family: "Open Sans", Arial, sans-serif;
    display: flex;
    justify-content: center;
    align-items: center;
  }
  .letterhead {
    position: relative;
    width: 622px;
    height: 880px;
    background: var(--paper);
    box-shadow: 0 4px 18px rgba(0,0,0,0.12);
    overflow: hidden;
  }
  .brand {
    position: absolute;
    top: 52px;
    left: 52px;
    display: flex;
    align-items: center;
    gap: 10px;
  }
  .brand-dot {
    width: 34px;
    height: 34px;
    border-radius: 50%;
    background: var(--brand-blue);
  }
  .brand-name {
    font-weight: 700;
    font-size: 15px;
    color: var(--brand-blue);
    letter-spacing: 1.5px;
    text-transform: uppercase;
  }
  .contact-list {
    position: absolute;
    top: 50px;
    right: 52px;
    list-style: none;
    text-align: right;
    font-size: 9.5px;
    line-height: 15px;
    color: var(--text-grey);
  }
  .contact-list li { display: flex; justify-content: flex-end; align-items: center; gap: 6px; }
  .contact-icon { width: 11px; height: 11px; }
  .letter-body {
    position: absolute;
    top: 200px;
    left: 52px;
    right: 64px;
    color: var(--text-grey);
    font-size: 11px;
    line-height: 15.5px;
  }
  .salutation {
    font-weight: 700;
    font-size: 14px;
    color: var(--heading-grey);
    margin-bottom: 12px;
  }
  .letter-body p { margin-bottom: 14px; }
  .signature {
    display: block;
    width: 120px;
    height: 46px;
    margin-top: 14px;
    background: linear-gradient(90deg, var(--signature-tone), #eeeff1);
    border-radius: 4px;
  }
  .footer-band {
    position: absolute;
    left: 0;
    top: 0;
    width: 622px;
    height: 880px;
    pointer-events: none;
  }
  .service-line {
    position: absolute;
    top: 808px;
    left: 356px;
    right: 10px;
    height: 26px;
    line-height: 26px;
    font-size: 10.5px;
    color: var(--paper);
    text-align: right;
    white-space: nowrap;
  }
</style>
</head>
<body>
  <main class="letterhead">
    <header>
      <div class="brand">
        <span class="brand-dot"></span>
        <span class="brand-name">Northgate Exteriors</span>
      </div>
      <ul class="contact-list">
        <li>555-010-2866
          <svg class="contact-icon" viewBox="0 0 12 12"><circle cx="6" cy="6" r="6" fill="var(--brand-blue)"/><path d="M4 3.2l1 .2.4 1.4-.7.6a4 4 0 0 0 1.9 1.9l.6-.7 1.4.4.2 1c-.3.6-1 .8-1.6.6A5.4 5.4 0 0 1 3.4 4.8c-.2-.6 0-1.3.6-1.6z" fill="#fff"/></svg>
        </li>
        <li>555-010-1568
          <svg class="contact-icon" viewBox="0 0 12 12"><circle cx="6" cy="6" r="6" fill="var(--brand-blue)"/><rect x="3" y="4" width="6" height="4" fill="#fff"/></svg>
        </li>
        <li>info@northgateexteriors.com
          <svg class="contact-icon" viewBox="0 0 12 12"><circle cx="6" cy="6" r="6" fill="var(--brand-blue)"/><rect x="3" y="4" width="6" height="4.2" fill="none" stroke="#fff" stroke-width="0.9"/><path d="M3 4l3 2.3L9 4" fill="none" stroke="#fff" stroke-width="0.9"/></svg>
        </li>
        <li>www.northgateexteriors.com
          <svg class="contact-icon" viewBox="0 0 12 12"><circle cx="6" cy="6" r="5.4" fill="none" stroke="var(--brand-blue)" stroke-width="1.2"/><ellipse cx="6" cy="6" rx="2.2" ry="5" fill="none" stroke="var(--brand-blue)" stroke-width="0.8"/><path d="M1 6h10" stroke="var(--brand-blue)" stroke-width="0.8"/></svg>
        </li>
      </ul>
    </header>

    <section class="letter-body">
      <p class="salutation">Dear Mr. John,</p>
      <p>Lorem Ipsum is simply dummy text of the printing and typesetting industry. Lorem Ipsum has been the industry's standard dummy text ever since the 1500s, when an unknown printer took a galley of type and scrambled it to make a type specimen book. It has survived not only five centuries, but also the leap into electronic typesetting, remaining essentially unchanged.</p>
      <p>The standard chunk of Lorem Ipsum used since the 1500s is reproduced below for those interested. Sections 1.10.32 and 1.10.33 from "de Finibus Bonorum et Malorum" by Cicero are also reproduced in their exact original form, accompanied by English versions from the 1914 translation by H. Rackham.</p>
      <p>Lorem Ipsum is simply dummy text of the printing and typesetting industry. Lorem Ipsum has been the industry's standard dummy text ever since the 1500s, when an unknown printer took a galley of type and scrambled it to make a type specimen book. It has survived not only five centuries, but also the leap into electronic typesetting, remaining essentially unchanged. It was popularised in the</p>
      <span class="signature" role="img" aria-label="Handwritten signature of the sender"></span>
    </section>

    <footer>
      <svg class="footer-band" viewBox="0 0 622 880" aria-hidden="true">
        <polygon points="0,868 286,868 316,838 622,838 622,845 319,845 289,875 0,875" fill="var(--brand-grey)"/>
        <polygon points="328,808 336,808 310,834 302,834" fill="var(--brand-grey)"/>
        <polygon points="342,808 352,808 326,834 316,834" fill="var(--brand-grey)"/>
        <polygon points="366,808 622,808 622,834 340,834" fill="var(--brand-blue)"/>
      </svg>
      <p class="service-line">Storm Restoration | Roofing | Siding | Windows</p>
    </footer>
  </main>
</body>
</html>
```